Veranix - Solution provider in business consulting

Veranix is a swiss based company providing solutions for developing markets. The business covers various fields of business consulting, such as supply chain, product costs, quality management and manufacturing management. The Business operates in a efficient, straight and solution oriented manner.
The final design should communicate these characteristics. Asian people as well as as western people shall identify the qualities of the company at first sight.
The customer needs business cards with a simple view but an recognizable design, printed in high quality. Engraved elements such as the globe or simple words are possible.
Available colors are: (RAL)
102/102/102
51/102/102
153/204/153
255/102/51
Font: Calibri

```html
<!DOCTYPE html>
<html lang="en">
<head>
<meta charset="utf-8">
<title>Veranix – Business Card</title>
<link rel="stylesheet" href="https://fonts.googleapis.com/css2?family=Carlito:wght@400;700&display=swap">
<style>
  :root {
    --sheet: #ffffff;
    --card-sky: #92d6f3;
    --band-teal: #76c3dc;
    --brand-grey: #666666;
    --ink-navy: #1b2b6b;
    --trim-line: #000000;
  }
  * { margin: 0; padding: 0; box-sizing: border-box; }
  html, body {
    width: 1200px;
    height: 843px;
    overflow: hidden;
    background: var(--sheet);
  }
  .print-sheet {
    position: relative;
    width: 1200px;
    height: 843px;
    background: var(--sheet);
    font-family: "Carlito", "Calibri", sans-serif;
  }
  .crop-marks {
    position: absolute;
    inset: 0;
  }
  .crop-marks line {
    stroke: var(--trim-line);
    stroke-width: 1;
  }
  .business-card {
    position: absolute;
    left: 98px;
    top: 135px;
    width: 1001px;
    height: 572px;
    background: var(--card-sky);
    overflow: hidden;
  }
  .brand-band {
    position: absolute;
    left: 157px;
    top: 0;
    width: 62px;
    height: 100%;
    background: var(--band-teal);
  }
  .brand-name {
    position: absolute;
    left: 188px;
    top: 284px;
    transform: translate(-50%, -50%) rotate(-90deg);
    font-size: 74px;
    font-weight: 400;
    letter-spacing: 2px;
    line-height: 1;
    color: var(--brand-grey);
    white-space: nowrap;
  }
  .contact-block {
    position: absolute;
    right: 120px;
    top: 81px;
    text-align: right;
    color: var(--ink-navy);
    font-size: 29px;
    line-height: 35.7px;
  }
  .contact-block p { white-space: nowrap; }
  .person-name { font-weight: 700; }
  .company-address,
  .contact-lines { margin-top: 28px; }
</style>
</head>
<body>
  <div class="print-sheet">
    <svg class="crop-marks" width="1200" height="843" viewBox="0 0 1200 843" aria-hidden="true">
      <!-- top left -->
      <line x1="85" y1="0" x2="85" y2="71"/>
      <line x1="117" y1="34" x2="117" y2="92"/>
      <line x1="0" y1="83" x2="71" y2="83"/>
      <line x1="35" y1="116" x2="92" y2="116"/>
      <!-- top right -->
      <line x1="1115" y1="0" x2="1115" y2="71"/>
      <line x1="1083" y1="34" x2="1083" y2="92"/>
      <line x1="1129" y1="83" x2="1200" y2="83"/>
      <line x1="1105" y1="116" x2="1165" y2="116"/>
      <!-- bottom left -->
      <line x1="85" y1="772" x2="85" y2="843"/>
      <line x1="117" y1="750" x2="117" y2="808"/>
      <line x1="0" y1="759" x2="71" y2="759"/>
      <line x1="35" y1="724" x2="92" y2="724"/>
      <!-- bottom right -->
      <line x1="1115" y1="772" x2="1115" y2="843"/>
      <line x1="1083" y1="750" x2="1083" y2="808"/>
      <line x1="1129" y1="759" x2="1200" y2="759"/>
      <line x1="1105" y1="724" x2="1165" y2="724"/>
    </svg>

    <section class="business-card">
      <div class="brand-band"></div>
      <div class="brand-name">veranix</div>

      <div class="contact-block">
        <p class="person-name">Marco Lenz</p>
        <p class="person-role">CEO</p>

        <div class="company-address">
          <p>Veranix GmbH</p>
          <p>Lindenrain 14</p>
          <p>9238 Talheim</p>
          <p>Switzerland</p>
        </div>

        <div class="contact-lines">
          <p>Mobile +41 79 555 0182</p>
          <p>Phone +41 71 555 0147</p>
          <p>marco.lenz@veranix.ch</p>
          <p>www.veranix.ch</p>
        </div>
      </div>
    </section>
  </div>
</body>
</html>
```